Verlindo Magician

I want the business card for my business to give to people who watch that later I will be employed to show magic here is my website http://www.verlindoillusions.example/I want the interesting design , i am very opened for formal and informal, I watch a lot of design so don't stick to the common shape and form but i hope it can also be produced the thing to write on will be the same as in picture that i will upload , i also will upload the logo for you that so can be easy to useDenis CostilleMagicianMAGICIAN VERLINDO 17 rue des Tilleuls - 25000 BESANÇON contact@verlindoillusions.example tel. 0381 946 157 tel. 0674 219 503

```html
<!DOCTYPE html>
<html lang="en">
<head>
<meta charset="utf-8">
<title>Verlindo Magician – Business Card</title>
<link href="https://fonts.googleapis.com/css2?family=Poppins:wght@400&family=Jost:wght@400&display=swap" rel="stylesheet">
<style>
  :root {
    --page-bg: #ebe8e4;
    --card-white: #ffffff;
    --ink: #111111;
    --text-grey: #555555;
    --accent-red: #e8202a;
    --rule: #222222;
    --back-tint-a: #f7f2f2;
    --back-tint-b: #f1eeee;
    --figure-dark: #161616;
    --figure-mid: #3a3a3a;
  }
  * { box-sizing: border-box; margin: 0; padding: 0; }
  html, body { width: 1125px; height: 1200px; overflow: hidden; }
  body { background: var(--page-bg); position: relative; font-family: "Poppins", sans-serif; }

  .card {
    position: absolute;
    left: 162px;
    width: 800px;
    height: 456px;
    box-shadow: 0 2px 6px rgba(0,0,0,0.18);
  }
  .card--front { top: 90px; background: var(--card-white); }
  .card--back {
    top: 612px;
    background: linear-gradient(135deg, var(--back-tint-a), var(--back-tint-b));
  }

  .brand-figure {
    position: absolute;
    background: linear-gradient(180deg, var(--figure-mid) 0%, var(--figure-dark) 60%);
    border-radius: 40px 40px 18px 18px;
  }
  .card--front .brand-figure { left: 95px; top: 98px; width: 168px; height: 210px; }
  .card--back .brand-figure { left: 287px; top: 74px; width: 228px; height: 286px; }

  .brand-name {
    position: absolute;
    left: 60px;
    top: 308px;
    width: 240px;
    text-align: center;
    font-family: "Jost", sans-serif;
    font-weight: 400;
    font-size: 34px;
    letter-spacing: 1px;
    color: var(--ink);
  }

  .divider {
    position: absolute;
    left: 303px;
    top: 104px;
    width: 1px;
    height: 248px;
    background: var(--rule);
  }

  .contact {
    position: absolute;
    left: 343px;
    top: 108px;
    color: var(--text-grey);
  }
  .contact__name { font-size: 28px; line-height: 36px; color: var(--ink); }
  .contact__role { font-size: 21px; line-height: 24px; color: var(--accent-red); }
  .contact__company { margin-top: 18px; font-size: 18px; line-height: 24px; }
  .contact__list { list-style: none; margin-top: 14px; }
  .contact__list li {
    display: flex; align-items: center; gap: 10px;
    font-size: 18.5px; line-height: 25.5px;
  }
  .contact__list svg { width: 18px; height: 18px; fill: var(--ink); flex: none; }

  .back-url {
    position: absolute;
    left: 0; right: 0;
    top: 392px;
    text-align: center;
    font-family: "Jost", sans-serif;
    font-size: 20px;
    letter-spacing: 3px;
    color: var(--text-grey);
  }
</style>
</head>
<body>
  <section class="card card--front">
    <div class="brand-figure" role="img" aria-label="Black and white illustration of the magician holding a playing card"></div>
    <div class="brand-name">VERLINDO</div>
    <div class="divider"></div>
    <div class="contact">
      <h1 class="contact__name" style="font-weight:400">MARC RAVOULET</h1>
      <p class="contact__role">Magician</p>
      <p class="contact__company">MAGICIAN VERLINDO<br>17 rue des Tilleuls - 25000 BESANÇON</p>
      <ul class="contact__list">
        <li><svg viewBox="0 0 24 24" aria-hidden="true"><path d="M6.6 10.8a15.1 15.1 0 0 0 6.6 6.6l2.2-2.2a1 1 0 0 1 1-.25 11.4 11.4 0 0 0 3.6.57 1 1 0 0 1 1 1V20a1 1 0 0 1-1 1A17 17 0 0 1 3 4a1 1 0 0 1 1-1h3.5a1 1 0 0 1 1 1c0 1.25.2 2.45.57 3.57a1 1 0 0 1-.25 1z"/></svg>0381 946 157</li>
        <li><svg viewBox="0 0 24 24" aria-hidden="true"><path d="M6.6 10.8a15.1 15.1 0 0 0 6.6 6.6l2.2-2.2a1 1 0 0 1 1-.25 11.4 11.4 0 0 0 3.6.57 1 1 0 0 1 1 1V20a1 1 0 0 1-1 1A17 17 0 0 1 3 4a1 1 0 0 1 1-1h3.5a1 1 0 0 1 1 1c0 1.25.2 2.45.57 3.57a1 1 0 0 1-.25 1z"/></svg>0674 219 503</li>
        <li><svg viewBox="0 0 24 24" aria-hidden="true"><path d="M3 6h18v12H3z M3 6l9 7 9-7" fill="none" stroke="#111" stroke-width="0"/><path d="M3 6h18l-9 7z"/><path d="M3 8l9 7 9-7v10H3z"/></svg>contact@verlindoillusions.example</li>
        <li><svg viewBox="0 0 24 24" aria-hidden="true"><circle cx="12" cy="12" r="9"/></svg>www.verlindoillusions.example</li>
      </ul>
    </div>
  </section>

  <section class="card card--back">
    <div class="brand-figure" role="img" aria-label="Large illustration of the magician holding a playing card over a soft card-suit backdrop"></div>
    <p class="back-url">WWW.VERLINDOILLUSIONS.EXAMPLE</p>
  </section>
</body>
</html>
```